Billboard design 8x3M RAVU (Spanish company)

We´re located in the south of Spain. We run a local telecom company.
We sell Fiber optic, and mobile phone lines mainly.
The billboard will have to be in Spanish, I would like the price to be something you spot on first sight when passing by in the car.
Our company color is blue, like in our logo which I will add. I will also add a example from what we currently have.
The new offer should be:
1000 megas + 100Gigas movil con llamadas ilimitadas. (meaning 1000Mb fiber optic speed and 100Gb data and unlimited calls for 1 mobile line)
Our details are: phone line 958 47 6620
Website: ra-vu.es

```html
<!DOCTYPE html>
<html lang="es">
<head>
<meta charset="utf-8">
<title>RAVU – Valla 8x3</title>
<link rel="stylesheet" href="https://fonts.googleapis.com/css2?family=Saira+Semi+Condensed:wght@600;700;800&display=swap">
<style>
  :root {
    --navy: #04588a;
    --navy-deep: #064b74;
    --sky: #00c4fb;
    --white: #ffffff;
    --page: #e7edf3;
  }
  * { margin: 0; padding: 0; box-sizing: border-box; }
  html, body {
    width: 1200px; height: 800px; overflow: hidden;
    background: var(--page);
    font-family: "Saira Semi Condensed", "Arial Narrow", sans-serif;
  }
  .billboard {
    position: absolute; left: 40px; top: 150px;
    width: 1120px; height: 500px;
    background: var(--white);
    overflow: hidden;
    box-shadow: 0 10px 30px rgba(6, 45, 75, 0.18);
  }
  .billboard-shapes { position: absolute; inset: 0; }
  .price {
    position: absolute; left: 0; top: 95px; width: 285px;
    text-align: center; color: var(--white);
  }
  .price-amount {
    display: block; font-size: 150px; font-weight: 800;
    line-height: 0.9; letter-spacing: -5px;
  }
  .price-label {
    display: block; font-size: 44px; font-weight: 700;
    line-height: 1; margin-top: 10px;
  }
  .brand {
    position: absolute; left: 500px; top: 22px; width: 320px;
    text-align: center;
  }
  .brand-name {
    display: block; font-size: 90px; font-weight: 800;
    line-height: 1; color: var(--sky); letter-spacing: 2px;
  }
  .brand-services {
    display: block; font-size: 24px; font-weight: 700;
    color: var(--navy-deep); margin-top: 4px;
  }
  .offer {
    position: absolute; left: 350px; top: 165px; width: 740px;
  }
  .offer-main {
    display: block; font-size: 56px; font-weight: 700;
    line-height: 1.05; color: var(--navy-deep); white-space: nowrap;
  }
  .offer-sub {
    display: block; font-size: 36px; font-weight: 700;
    line-height: 1.2; color: var(--sky); white-space: nowrap; margin-top: 6px;
  }
  .contact-phone {
    position: absolute; left: 28px; top: 382px;
    display: flex; align-items: center; gap: 14px;
  }
  .phone-icon { width: 58px; height: 58px; flex: none; }
  .phone-number {
    font-size: 80px; font-weight: 700; line-height: 1;
    color: var(--navy-deep); letter-spacing: 1px; white-space: nowrap;
  }
  .contact-web {
    position: absolute; left: 660px; top: 350px; width: 440px;
    text-align: right;
    font-size: 66px; font-weight: 700; line-height: 1;
    color: var(--white); white-space: nowrap;
  }
</style>
</head>
<body>
  <main class="billboard">
    <svg class="billboard-shapes" viewBox="0 0 1120 500" width="1120" height="500" aria-hidden="true">
      <rect x="0" y="350" width="1120" height="150" fill="var(--sky)"/>
      <path d="M545 325 H1120 V452 H700 C655 452 640 430 624 392 C607 350 590 325 545 325 Z" fill="var(--navy)"/>
      <path d="M0 0 H240 C285 90 305 220 288 350 H0 Z" fill="var(--navy)"/>
      <path d="M258 0 C303 90 323 220 306 350" fill="none" stroke="var(--navy)" stroke-width="4" stroke-dasharray="10 7"/>
    </svg>

    <div class="price">
      <span class="price-amount">35€</span>
      <span class="price-label">Por sólo</span>
    </div>

    <header class="brand">
      <span class="brand-name">RAVU</span>
      <span class="brand-services">Wifi | Fibra | Movil | Tv</span>
    </header>

    <section class="offer">
      <span class="offer-main">1000 MEGAS + 100GIGAS</span>
      <span class="offer-sub">MOVIL CON LLAMADAS ILIMITADAS</span>
    </section>

    <div class="contact-phone">
      <svg class="phone-icon" viewBox="0 0 60 60" aria-hidden="true">
        <circle cx="30" cy="30" r="30" fill="var(--navy-deep)"/>
        <path d="M20 16 l6 -2 l5 10 l-4 3 c2 5 5 8 10 10 l3 -4 l10 5 l-2 6 c-16 1 -29 -12 -28 -28 z" fill="var(--white)"/>
        <path d="M36 18 a8 8 0 0 1 7 7 M37 12 a14 14 0 0 1 12 12" fill="none" stroke="var(--white)" stroke-width="2.5" stroke-linecap="round"/>
      </svg>
      <span class="phone-number">958 47 6620</span>
    </div>

    <div class="contact-web">www.ra-vu.es</div>
  </main>
</body>
</html>
```